Spy/Espionage/Counterintelligence Membership Community Needs a PowerPoint Template

We need a powerpoint template for one of our business verticals focused on spies, espionage, and counterintelligence. The name of it is "Brass Lantern Guild" and the logo is attached. Brass Lantern Guild is a community that connects people with experts in espionage and counterintelligence through an online social network, as well as in-person events. We would like to see designs that incorporate the red and black of the logo. The design should communicate mystery/suspense and peak curiosity.

Target Market(s)

Late 20s to baby boomers, male

Industry/Entity Type

Social Club

Font styles to use
Sans Serif

Colors
ec1f27
000000
ffffff

Requirements
Must have
• A user-friendly ppt template file. Incorporate basic fonts that don't have to be installed on every computer for presentations. A cover slide and a basic inside slide. A white background. I will also need graphic source files.
Nice to have
• Plenty of space for slide title and body content. Logo on every slide.
Should not have
• Inconsistency with fonts. Misalignment of images.

```html
<!DOCTYPE html>
<html lang="en">
<head>
<meta charset="utf-8">
<title>Brass Lantern Guild – Inside Slide</title>
<link rel="stylesheet" href="https://fonts.googleapis.com/css2?family=PT+Sans+Narrow:wght@400;700&family=Open+Sans:ital,wght@1,400&display=swap">
<style>
  :root {
    --ink: #1a1a1a;
    --black: #000000;
    --white: #ffffff;
    --title-red: #a3070d;
    --heading-red: #c0101a;
    --brand-red: #ec1f27;
    --deep-red: #7d0006;
    --paper: #fbfbfb;
  }
  * { margin: 0; padding: 0; box-sizing: border-box; }
  html, body { width: 1200px; height: 900px; overflow: hidden; background: var(--white); }
  .slide {
    position: relative;
    width: 1200px;
    height: 900px;
    overflow: hidden;
    background:
      radial-gradient(circle at 600px 420px, rgba(236,31,39,0.07) 0, rgba(236,31,39,0.04) 200px, rgba(255,255,255,0) 290px),
      linear-gradient(180deg, #f4f4f4 0%, var(--paper) 40%, var(--white) 100%);
    font-family: "PT Sans Narrow", "Arial Narrow", sans-serif;
    color: var(--ink);
  }
  .title-tab {
    position: absolute;
    left: 0; top: 22px;
    width: 46px; height: 66px;
  }
  .slide-title {
    position: absolute;
    left: 60px; top: 26px;
    font-size: 50px;
    font-weight: 700;
    color: var(--title-red);
    letter-spacing: -0.3px;
    line-height: 1.1;
  }
  .section-heading {
    position: absolute;
    left: 88px; top: 147px;
    font-size: 34px;
    font-weight: 700;
    color: var(--heading-red);
    line-height: 1.1;
  }
  .feature-list {
    position: absolute;
    left: 92px; top: 206px;
    width: 960px;
    list-style: none;
  }
  .feature-list li {
    position: relative;
    padding-left: 43px;
    font-size: 24px;
    line-height: 39px;
    color: var(--ink);
  }
  .feature-list .tick {
    position: absolute;
    left: 0; top: 8px;
    width: 28px; height: 26px;
  }
  .brand-name {
    position: absolute;
    right: 14px; top: 745px;
    font-size: 40px;
    font-weight: 400;
    color: var(--black);
    letter-spacing: -0.5px;
    line-height: 1;
  }
  .footer {
    position: absolute;
    left: 0; bottom: 0;
    width: 1200px; height: 93px;
    border-top: 4px solid var(--black);
    background: linear-gradient(180deg, #e3141c 0%, #c40a12 45%, var(--deep-red) 100%);
  }
  .page-number {
    position: absolute;
    left: 33px; top: 16px;
    width: 60px; height: 58px;
    background: var(--black);
    border: 2px solid #3a3a3a;
    border-radius: 4px;
    color: var(--white);
    font-family: "Open Sans", Arial, sans-serif;
    font-style: normal;
    font-size: 30px;
    line-height: 54px;
    text-align: center;
  }
  .tagline {
    position: absolute;
    left: 130px; top: 27px;
    font-family: "Open Sans", Arial, sans-serif;
    font-style: italic;
    font-size: 26px;
    color: var(--white);
    line-height: 1.3;
  }
  .nav-button {
    position: absolute;
    top: 16px;
    height: 58px;
    background: var(--black);
    color: var(--white);
    font-family: "Open Sans", Arial, sans-serif;
    font-size: 23px;
    line-height: 58px;
    text-align: center;
  }
  .nav-back {
    left: 957px; width: 108px;
    clip-path: polygon(18px 0, 100% 0, 100% 100%, 18px 100%, 0 50%);
    padding-left: 8px;
  }
  .nav-next {
    left: 1074px; width: 100px;
    clip-path: polygon(0 0, calc(100% - 18px) 0, 100% 50%, calc(100% - 18px) 100%, 0 100%);
    padding-right: 10px;
  }
</style>
</head>
<body>
<main class="slide">
  <svg class="title-tab" viewBox="0 0 46 66" aria-hidden="true">
    <defs>
      <linearGradient id="tabRed" x1="0" y1="0" x2="0" y2="1">
        <stop offset="0" stop-color="#ec1f27"/>
        <stop offset="1" stop-color="#8e0008"/>
      </linearGradient>
    </defs>
    <polygon points="0,0 46,0 28,33 46,66 0,66" fill="url(#tabRed)"/>
  </svg>

  <h1 class="slide-title">Presentation Title</h1>
  <h2 class="section-heading">Something About Your Business</h2>

  <ul class="feature-list">
    <li><svg class="tick" viewBox="0 0 28 26" aria-hidden="true"><rect x="2" y="6" width="18" height="18" fill="none" stroke="#a3070d" stroke-width="2.5"/><path d="M6 14 L11 20 L26 2" fill="none" stroke="#a3070d" stroke-width="4" stroke-linecap="round" stroke-linejoin="round"/></svg>High volume local boutique real estate company</li>
    <li><svg class="tick" viewBox="0 0 28 26" aria-hidden="true"><rect x="2" y="6" width="18" height="18" fill="none" stroke="#a3070d" stroke-width="2.5"/><path d="M6 14 L11 20 L26 2" fill="none" stroke="#a3070d" stroke-width="4" stroke-linecap="round" stroke-linejoin="round"/></svg>Specialize in selling homes throughout the San Francisco Bay Area</li>
    <li><svg class="tick" viewBox="0 0 28 26" aria-hidden="true"><rect x="2" y="6" width="18" height="18" fill="none" stroke="#a3070d" stroke-width="2.5"/><path d="M6 14 L11 20 L26 2" fill="none" stroke="#a3070d" stroke-width="4" stroke-linecap="round" stroke-linejoin="round"/></svg>Focus on modern marketing techniques and thinking outside the box</li>
    <li><svg class="tick" viewBox="0 0 28 26" aria-hidden="true"><rect x="2" y="6" width="18" height="18" fill="none" stroke="#a3070d" stroke-width="2.5"/><path d="M6 14 L11 20 L26 2" fill="none" stroke="#a3070d" stroke-width="4" stroke-linecap="round" stroke-linejoin="round"/></svg>“High Tech and High Touch” approach to real estate</li>
    <li><svg class="tick" viewBox="0 0 28 26" aria-hidden="true"><rect x="2" y="6" width="18" height="18" fill="none" stroke="#a3070d" stroke-width="2.5"/><path d="M6 14 L11 20 L26 2" fill="none" stroke="#a3070d" stroke-width="4" stroke-linecap="round" stroke-linejoin="round"/></svg>Certified Green Business Everything is done and stored online. No File Cabinets in our offices!</li>
    <li><svg class="tick" viewBox="0 0 28 26" aria-hidden="true"><rect x="2" y="6" width="18" height="18" fill="none" stroke="#a3070d" stroke-width="2.5"/><path d="M6 14 L11 20 L26 2" fill="none" stroke="#a3070d" stroke-width="4" stroke-linecap="round" stroke-linejoin="round"/></svg>Exceptional web presence far beyond other local real estate companies</li>
    <li><svg class="tick" viewBox="0 0 28 26" aria-hidden="true"><rect x="2" y="6" width="18" height="18" fill="none" stroke="#a3070d" stroke-width="2.5"/><path d="M6 14 L11 20 L26 2" fill="none" stroke="#a3070d" stroke-width="4" stroke-linecap="round" stroke-linejoin="round"/></svg>Clean, streamline, and hip marketing materials</li>
    <li><svg class="tick" viewBox="0 0 28 26" aria-hidden="true"><rect x="2" y="6" width="18" height="18" fill="none" stroke="#a3070d" stroke-width="2.5"/><path d="M6 14 L11 20 L26 2" fill="none" stroke="#a3070d" stroke-width="4" stroke-linecap="round" stroke-linejoin="round"/></svg>A company constantly looking into the latest real estate trends, tools, and technology to better<br>assist their agents and clients sell homes in the modern world, all while embracing tried and true<br>real estate values and practices as well</li>
    <li><svg class="tick" viewBox="0 0 28 26" aria-hidden="true"><rect x="2" y="6" width="18" height="18" fill="none" stroke="#a3070d" stroke-width="2.5"/><path d="M6 14 L11 20 L26 2" fill="none" stroke="#a3070d" stroke-width="4" stroke-linecap="round" stroke-linejoin="round"/></svg>Leading authority for architectural homes and recognized world wide</li>
    <li><svg class="tick" viewBox="0 0 28 26" aria-hidden="true"><rect x="2" y="6" width="18" height="18" fill="none" stroke="#a3070d" stroke-width="2.5"/><path d="M6 14 L11 20 L26 2" fill="none" stroke="#a3070d" stroke-width="4" stroke-linecap="round" stroke-linejoin="round"/></svg>Not Just Modern Homes! We focus on Modern Real Estate<br>Practices through and through.</li>
  </ul>

  <div class="brand-name">Brass Lantern Guild</div>

  <footer class="footer">
    <div class="page-number">03</div>
    <p class="tagline">tagline/slogan about your company</p>
    <div class="nav-button nav-back">Back</div>
    <div class="nav-button nav-next">Next</div>
  </footer>
</main>
</body>
</html>
```